Basic / Quick Business Card

Quick easy design project!

Need a one sided basic business card that matches font & style of brand and bottle label for our gourmet condiment, Brindle Harrow Sauce. Brindle Harrow Sauce is sold in specialty retail, gourmet groceries and appears on chef-driven restaurant menus, so the target market is a high end, gourmet, artisan-made food-loving customer.

Files Included:
Sauce Bottle Label
Brindle Harrow Sauce Round Logos

**About the logos - the logo may be used in a circle or alone vertically as on side of the bottle label**

Layout of Card:
May be vertical or horizontal based on designer ideas.

Logo usage (in circle vs. stand alone vertical logo) is up to designers descretion as well.

Reverse side of business card will be various high end / professional product photos / food shots using us.kelbo.com system. **Designer on this project will NOT design a reserve for the card.**

Paper that will be used for printing:
Kelbo Standard - it's a WHITE paper, but we use a cream background on Brindle Harrow Sauce branding, so please take this into account on design to stay brand consistent.

Elements & Copy for Card:
1. Logo in either script horizontal or vertical version
2. Copy: "Artisan Made - Small Batch"
3. Name - Wes Dorrance
4. Title - Creator
5. Phone - xxx.xxx.xxxx
6. xxxx@brindleharrow.com
7. URL: brindleharrowsauce.com
8. Social Media: @getbrindleharrow on Quillo / Pagora / Lumigrid

Please provide final files in Illustrator or InDesign format.

```html
<!DOCTYPE html>
<html lang="en">
<head>
<meta charset="utf-8">
<title>Brindle Harrow Sauce — Business Card</title>
<link rel="stylesheet" href="https://fonts.googleapis.com/css2?family=Special+Elite&family=Yellowtail&display=swap">
<style>
  :root {
    --page: #e8e5e2;
    --gold: #e9a317;
    --gold-deep: #d58f0c;
    --cream: #f1eedf;
    --ink: #141414;
    --ink-soft: #262626;
    --muted: #5c5c5c;
  }
  * { box-sizing: border-box; margin: 0; padding: 0; }
  html, body {
    width: 1200px; height: 867px; overflow: hidden;
    background: var(--page);
  }
  .card {
    position: absolute; left: 40px; top: 113px;
    width: 1120px; height: 640px;
    background: linear-gradient(180deg, var(--gold) 0%, var(--gold-deep) 100%);
    padding: 20px;
  }
  .card__frame {
    width: 100%; height: 100%;
    background: var(--cream);
    padding: 9px;
  }
  .card__panel {
    position: relative; width: 100%; height: 100%;
    background: linear-gradient(125deg, var(--ink) 0%, var(--ink-soft) 55%, var(--ink) 100%);
    font-family: "Special Elite", "Courier New", monospace;
  }
  .card__dashes { position: absolute; inset: 0; }
  .tagline {
    position: absolute; right: 44px; top: 8px;
    padding: 0 14px;
    background: var(--ink);
    color: var(--gold);
    font-size: 22px; letter-spacing: 0.5px;
  }
  .brand {
    position: absolute; left: 90px; top: 200px; width: 380px;
    color: var(--cream);
    font-size: 54px; line-height: 1.15;
    text-align: center;
  }
  .contact {
    position: absolute; left: 573px; top: 175px;
    color: var(--cream);
  }
  .contact__name {
    font-family: "Yellowtail", cursive;
    color: var(--gold);
    font-size: 46px; line-height: 1;
  }
  .contact__title {
    color: var(--gold);
    font-size: 23px; margin-top: 10px;
  }
  .contact__list {
    list-style: none; margin-top: 54px;
    font-size: 24px; line-height: 38px;
  }
  .social {
    position: absolute; left: 62px; right: 62px; top: 512px;
    display: flex; justify-content: space-between;
    list-style: none;
    color: var(--muted); font-size: 24px;
  }
  .social__item { display: flex; align-items: center; gap: 12px; }
  .social__mark {
    width: 26px; height: 26px; border-radius: 3px;
    background: var(--muted);
  }
</style>
</head>
<body>
  <article class="card">
    <div class="card__frame">
      <div class="card__panel">
        <svg class="card__dashes" width="1062" height="582" aria-hidden="true">
          <rect x="23" y="23" width="1016" height="536" fill="none"
                stroke="#f1eedf" stroke-width="3" stroke-dasharray="8 7"/>
        </svg>
        <p class="tagline">ARTISAN MADE - SMALL BATCH</p>

        <h1 class="brand">Brindle<br>Harrow<br>Sauce</h1>

        <section class="contact">
          <h2 class="contact__name">Wes Dorrance</h2>
          <p class="contact__title">Creator</p>
          <ul class="contact__list">
            <li>P. 123.456.7890</li>
            <li>E. dorrance@brindleharrow.com</li>
            <li>W. www.brindleharrowsauce.com</li>
          </ul>
        </section>

        <ul class="social">
          <li class="social__item"><span class="social__mark" aria-label="Quillo"></span>@getbrindleharrow</li>
          <li class="social__item"><span class="social__mark" aria-label="Lumigrid"></span>getbrindleharrow</li>
          <li class="social__item"><span class="social__mark" aria-label="Pagora"></span>getbrindleharrow</li>
        </ul>
      </div>
    </div>
  </article>
</body>
</html>
```